Business Card Design for a Personal Trainer

I need a business card design for my job as a personal trainer. It should have a unique, modern and exclusive design. On the front there should be only my logo with my name and my job. 0162/3819204 Tobias Lendhart Wiesengrundweg 14 80417 Munich Germany The most important contact information is the web adress. it can be bigger than the rest, but its not necessary. The card should be 8,5cmx5,5cm big. Font: Roboto. Colors: black, white, gray, 56c1ff.

```html
<!DOCTYPE html>
<html lang="de">
<head>
<meta charset="utf-8">
<title>Tobias Lendhart – Personal Trainer Visitenkarte</title>
<link href="https://fonts.googleapis.com/css2?family=Roboto:wght@300;400;700&display=swap" rel="stylesheet">
<style>
  :root {
    --backdrop: #5a5a5a;
    --card: #262626;
    --card-edge: #1c1c1c;
    --mark: #454545;
    --text: #ffffff;
    --muted: #5c5c5c;
    --accent: #56c1ff;
    --photo-light: #8a8a8a;
    --photo-dark: #2e2e2e;
  }
  * { box-sizing: border-box; margin: 0; padding: 0; }
  html, body {
    width: 1200px; height: 1021px; overflow: hidden;
    background: var(--backdrop);
    font-family: "Roboto", sans-serif;
  }
  .canvas { position: relative; width: 1200px; height: 1021px; }
  .card {
    position: absolute; left: 300px; width: 600px; height: 388px;
    background: var(--card);
    box-shadow: 0 10px 28px rgba(0,0,0,.45);
    overflow: hidden;
  }
  .card--front { top: 92px; }
  .card--back { top: 536px; }

  /* Front */
  .brand {
    position: absolute; inset: 0;
    display: flex; flex-direction: column; align-items: center; justify-content: center;
    gap: 10px;
  }
  .brand__name {
    font-weight: 400; font-size: 40px; letter-spacing: 3px;
    text-transform: uppercase; color: var(--mark);
  }
  .brand__role {
    display: flex; align-items: center; gap: 12px;
    font-weight: 300; font-size: 15px; letter-spacing: 9px;
    text-transform: uppercase; color: var(--muted);
  }
  .brand__rule { width: 60px; height: 1px; background: var(--muted); }

  /* Back */
  .portrait {
    position: absolute; left: 0; top: 0; bottom: 0; width: 270px;
    background: radial-gradient(ellipse at 55% 40%, var(--photo-light) 0%, #555 45%, var(--photo-dark) 100%);
  }
  .contact {
    position: absolute; left: 270px; right: 20px; top: 0; bottom: 0;
    display: flex; flex-direction: column; align-items: center; justify-content: center;
    color: var(--text); text-align: center;
  }
  .contact__web {
    color: var(--accent); font-weight: 700; font-size: 25px;
    margin-bottom: 40px;
  }
  .contact__line { font-weight: 400; font-size: 18px; line-height: 1.3; }
  .contact__divider {
    width: 64px; height: 2px; background: var(--accent);
    margin: 16px 0 14px;
  }
</style>
</head>
<body>
<main class="canvas">
  <section class="card card--front" aria-label="Vorderseite">
    <div class="brand">
      <span class="brand__name">Tobias Lendhart</span>
      <span class="brand__role"><span class="brand__rule"></span>Personal Trainer<span class="brand__rule"></span></span>
    </div>
  </section>

  <section class="card card--back" aria-label="Rückseite">
    <div class="portrait" role="img" aria-label="Schwarzweiß-Porträt des Trainers mit verschränkten Armen im Sportshirt"></div>
    <div class="contact">
      <p class="contact__web">www.tobiaslendhart.de</p>
      <p class="contact__line">0162/3819204</p>
      <p class="contact__line">t.lendhart@postfeld.de</p>
      <span class="contact__divider"></span>
      <p class="contact__line">Wiesengrundweg 14</p>
      <p class="contact__line">80417 München</p>
    </div>
  </section>
</main>
</body>
</html>
```